I need a business card design for a new business based in South West Australia.
I specialize in residential window cleaning & general handyman maintenance.

Dale Marsh - 412 SILVER HAWK DETAILING
- Window Cleaning
- House Maintenance

```html
<!DOCTYPE html>
<html lang="en">
<head>
<meta charset="utf-8">
<title>Silver Hawk Detailing – Business Card</title>
<link href="https://fonts.googleapis.com/css2?family=Open+Sans:wght@400;600&display=swap" rel="stylesheet">
<style>
  :root {
    --page-bg: #e9e7e3;
    --card-black: #161718;
    --card-black-soft: #2a2c2e;
    --sky-light: #9cc0e4;
    --sky-mid: #5f93c9;
    --sky-deep: #3f6fa6;
    --text-white: #f4f5f6;
    --text-grey: #d9dcdf;
  }
  * { margin: 0; padding: 0; box-sizing: border-box; }
  html, body {
    width: 1200px;
    height: 892px;
    overflow: hidden;
    background: var(--page-bg);
    font-family: "Open Sans", sans-serif;
  }
  .stage {
    position: relative;
    width: 1200px;
    height: 892px;
  }
  .card {
    position: absolute;
    left: 100px;
    top: 140px;
    width: 1000px;
    height: 611px;
    background: linear-gradient(160deg, var(--card-black-soft) 0%, var(--card-black) 55%);
    overflow: hidden;
    box-shadow: 0 10px 30px rgba(0,0,0,0.18);
  }
  .card-art {
    position: absolute;
    inset: 0;
    width: 100%;
    height: 100%;
  }
  .services {
    position: absolute;
    left: 70px;
    bottom: 90px;
    list-style: none;
    color: var(--text-grey);
    font-size: 30px;
    line-height: 1;
  }
  .services li {
    display: flex;
    align-items: center;
    gap: 18px;
    margin-top: 22px;
  }
  .service-mark {
    width: 24px;
    height: 28px;
    background: var(--text-grey);
    border-radius: 3px;
    opacity: 0.85;
  }
  .contact {
    position: absolute;
    right: 70px;
    top: 380px;
    text-align: right;
    color: var(--text-white);
  }
  .company-name {
    font-size: 36px;
    font-weight: 400;
    letter-spacing: 1.5px;
  }
  .person-name {
    margin-top: 18px;
    font-size: 40px;
    font-weight: 400;
  }
  .phone {
    margin-top: 10px;
    font-size: 28px;
    letter-spacing: 1px;
    display: flex;
    justify-content: flex-end;
    align-items: center;
    gap: 16px;
  }
  .phone-icon {
    width: 26px;
    height: 26px;
  }
</style>
</head>
<body>
  <main class="stage">
    <section class="card">
      <svg class="card-art" viewBox="0 0 1000 611" preserveAspectRatio="none">
        <defs>
          <linearGradient id="windowPhotoTone" x1="0" y1="0" x2="1" y2="1">
            <stop offset="0" stop-color="var(--sky-light)"/>
            <stop offset="0.5" stop-color="var(--sky-mid)"/>
            <stop offset="1" stop-color="var(--sky-deep)"/>
          </linearGradient>
        </defs>
        <path class="window-photo" role="img"
              aria-label="Photo of a squeegee wiping soapy water from a window pane"
              d="M0,0 H1000 V110 Q560,300 0,370 Z"
              fill="url(#windowPhotoTone)"/>
      </svg>

      <ul class="services">
        <li><span class="service-mark" role="img" aria-label="Fleur-de-lis ornament"></span>House Maintenance</li>
        <li><span class="service-mark" role="img" aria-label="Fleur-de-lis ornament"></span>Window Cleaning</li>
      </ul>

      <div class="contact">
        <p class="company-name">SILVER HAWK DETAILING</p>
        <p class="person-name">Dale Marsh</p>
        <p class="phone">0400 555 018
          <svg class="phone-icon" viewBox="0 0 24 24" aria-hidden="true">
            <rect x="0" y="0" width="24" height="24" rx="3" fill="var(--text-white)"/>
            <path d="M8 5 L10.5 5 L11.5 8.5 L10 9.8 C10.8 11.8 12.2 13.2 14.2 14 L15.5 12.5 L19 13.5 L19 16 C19 17.2 18 18 16.8 17.9 C10.6 17.3 6.7 13.4 6.1 7.2 C6 6 6.8 5 8 5 Z" fill="var(--card-black)"/>
          </svg>
        </p>
      </div>
    </section>
  </main>
</body>
</html>
```